TREVAL BUILDWORKS, LLC Webpage portfolio

I want to create a Website that allows my potential clients to browse my Skilled work via before and after photos. I want the website to enhance the work that I provide and potentially drive new business, or at least solidify my work.
I also do 3D CAD and Modeling of New Spaces and it would be nice to show some of that work from pencil design to 3D modeling, which I feel may help give me more clients.

The website needs to show a solid carpenter/company with the skills to get any project completed.

Types of Jobs - Custom Carpentry & Finishes, Kitchens, Baths, Basements, Decks, Porches, Whole House Renovation - Skilled Craftsmanship (Hardwood Flooring, Floor and Wall Tile) and much more...

Target Market(s)

Residential Home Renovation, Kitchen and Bath Renovation, Home Improvement

Industry/Entity Type

Residential Construction

Number of Pages Required

5+ page

Font styles to use
Sans Serif
Script

Requirements
Must have
• Similar to Plinvo.com, except for Treval Buildworks.
• Must be inviting.
• My Services Offered
• A way to reach me or contact me for estimates with some sort of Screening Questionare.
Nice to have
• Inviting Colors
Should not have
• Not sure at this time

```html
<!DOCTYPE html>
<html lang="en">
<head>
<meta charset="utf-8">
<title>Treval Buildworks — Design, build &amp; remodeling contractors</title>
<link href="https://fonts.googleapis.com/css2?family=Questrial&family=Open+Sans:wght@400;600;700&family=Great+Vibes&display=swap" rel="stylesheet">
<style>
:root{
  --blue:#1e88d6;
  --blue-dark:#1f3a5c;
  --navy:#18314f;
  --ink:#222a33;
  --text:#555c63;
  --muted:#8a9097;
  --grey-bg:#f4f4f4;
  --panel:#ececec;
  --light-blue:#eaf3fb;
  --white:#fff;
  --line:#dcdcdc;
}
*{box-sizing:border-box;margin:0;padding:0}
html,body{width:1200px;height:4724px;overflow:hidden}
body{font-family:"Open Sans",Arial,sans-serif;color:var(--text);background:var(--white);position:relative;font-size:12px}
h1,h2,h3,.heading{font-family:"Questrial",Arial,sans-serif;font-weight:400;color:var(--ink)}
.section{position:absolute;left:0;width:1200px}
.container{position:absolute;left:98px;width:1004px}
a{color:var(--blue);text-decoration:none}
.btn{display:inline-block;font-size:13px;text-align:center;border-radius:2px}
.center{text-align:center}

/* header */
.site-header{top:0;height:120px;border-top:4px solid var(--blue)}
.brand{position:absolute;left:104px;top:28px;display:flex;align-items:center;gap:10px}
.brand-mark{width:34px;height:34px;background:var(--navy)}
.brand-name{font-family:"Questrial",sans-serif;font-size:24px;color:var(--navy)}
.search{position:absolute;left:630px;top:30px;font-size:13px;color:var(--muted);display:flex;align-items:center;gap:8px}
.sign-in{position:absolute;left:996px;top:22px;display:flex;align-items:center;gap:12px;font-size:15px;color:var(--ink)}
.sign-in .avatar{width:36px;height:36px;border-radius:50%;background:var(--blue);display:flex;align-items:center;justify-content:center}
.main-nav{position:absolute;left:425px;top:82px;display:flex;gap:0;font-size:13px;color:var(--ink)}
.main-nav span{margin-right:36px}

/* hero */
.hero{top:120px;height:425px}
.hero-photo{position:absolute;inset:0;background:linear-gradient(120deg,#3a2516 0%,#6b4528 35%,#2b1c12 60%,#5a3a22 100%)}
.hero-shade{position:absolute;inset:0;background:rgba(0,0,0,.35)}
.hero-content{position:absolute;left:0;width:1200px;top:112px;text-align:center;color:#fff}
.hero-title{font-family:"Questrial",sans-serif;font-size:72px;color:#fff;letter-spacing:1px;line-height:1}
.hero-sub{font-family:"Questrial",sans-serif;font-size:26px;margin-top:8px}
.hero-actions{margin-top:34px;display:flex;justify-content:center;gap:32px}
.hero-actions .btn{width:190px;height:36px;line-height:34px;border:1px solid #fff;color:#fff;font-size:15px}
.hero-actions .btn.solid{background:var(--navy)}
.hero-actions .btn.ghost{background:rgba(24,49,79,.7)}
.hero-arrow{position:absolute;top:190px}

/* intro */
.intro{top:545px;height:479px}
.section-title{font-size:32px;text-align:center;color:var(--ink)}
.intro .section-title{position:absolute;top:66px;width:1200px}
.intro-text{position:absolute;top:114px;width:1200px;text-align:center;font-size:13px;line-height:25px}
.feature{position:absolute;top:200px;width:280px;text-align:center}
.feature svg{display:block;margin:0 auto}
.feature h3{font-family:"Open Sans",sans-serif;font-weight:700;font-size:17px;margin-top:16px}
.feature p{font-size:11.5px;line-height:18px;margin-top:8px}
.feature a{display:block;font-weight:700;font-size:11.5px;margin-top:10px}

/* jobs */
.jobs{top:1024px;height:504px;background:var(--grey-bg)}
.jobs .section-title{position:absolute;top:66px;width:1200px}
.job-card{position:absolute;top:135px;width:232px;height:290px;background:#fff;border:1px solid var(--line)}
.job-photo{height:198px;position:relative}
.job-label{position:absolute;left:0;right:0;bottom:0;height:28px;background:rgba(24,49,79,.85);color:#fff;font-weight:700;font-size:12px;line-height:28px;text-align:center}
.job-card p{font-size:11px;line-height:17px;text-align:center;padding:12px 18px 0}
.job-card a{display:block;text-align:center;font-size:11px;margin-top:4px}

/* before after */
.gallery{top:1528px;height:488px}
.gallery .section-title{position:absolute;top:72px;width:1200px}
.ba-pair{position:absolute;top:145px;width:472px;height:282px;display:flex;gap:0}
.ba-item{flex:1;position:relative}
.ba-photo{position:absolute;inset:0 0 40px 0}
.ba-tag{position:absolute;left:0;right:0;bottom:0;height:44px;background:var(--blue);color:#fff;font-family:"Questrial",sans-serif;font-size:18px;letter-spacing:1px;line-height:44px;text-align:center}

/* why */
.why{top:2032px;height:472px}
.why-art{position:absolute;left:0;top:0;width:567px;height:472px;background:linear-gradient(135deg,#f7f7f7,#e4e6e8)}
.why-panel{position:absolute;left:567px;top:0;width:633px;height:472px;background:var(--light-blue)}
.why-body{position:absolute;left:31px;top:72px;width:500px}
.why-body h2{font-size:30px}
.why-body h4{font-family:"Questrial",sans-serif;font-weight:400;font-size:18px;color:var(--ink);margin-top:10px}
.why-body p{font-size:11px;line-height:19px;margin-top:16px}
.why-body .btn{margin-top:30px;width:108px;height:34px;line-height:34px;background:var(--blue);color:#fff}

/* browse */
.browse{top:2567px;height:660px}
.browse-box{position:absolute;left:98px;top:16px;width:658px;height:262px;background:var(--panel);padding:26px 34px}
.browse-box h3{font-size:20px}
.browse-box p{font-size:11px;line-height:21px;margin-top:12px}
.cta-box{position:absolute;top:16px;left:788px;width:312px;height:262px;background:linear-gradient(135deg,#1c3a59,#2d5476);text-align:center;color:#fff;padding-top:58px}
.cta-box h3{color:#fff;font-size:26px;line-height:34px}
.cta-box .btn{margin-top:26px;width:108px;height:32px;line-height:30px;border:1px solid #fff;color:#fff}
.pro-card{position:absolute;top:306px;width:312px;height:340px;border:1px solid var(--line);border-bottom:3px solid var(--blue);background:#fff}
.pro-photo{height:222px}
.pro-card h4{font-size:14px;font-weight:700;color:var(--ink);padding:14px 14px 0}
.pro-card p{font-size:11px;line-height:18px;padding:6px 14px 0}
.pro-meta{display:flex;justify-content:space-between;font-size:9.5px;color:var(--ink);padding:12px 14px 0}

/* video */
.video{top:3292px;height:409px}
.video-bg{position:absolute;inset:0;background:linear-gradient(100deg,#111 0%,#2a2623 45%,#151311 100%)}
.video h2{position:absolute;top:135px;width:1200px;text-align:center;color:#fff;font-size:32px}
.play{position:absolute;left:570px;top:210px}

/* design */
.design{top:3701px;height:482px}
.design .section-title{position:absolute;top:78px;width:1200px}
.design .cta-box{top:148px;left:98px;height:256px}
.work-box{position:absolute;left:441px;top:148px;width:659px;height:256px;background:var(--panel);padding:26px 34px}
.work-box h3{font-size:20px}
.work-box p{font-size:11px;line-height:21px;margin-top:10px}

/* contact */
.contact{top:4183px;height:463px;background:var(--light-blue)}
.contact .section-title{position:absolute;top:92px;width:1200px}
.info{position:absolute;top:150px;display:flex;gap:16px}
.info-icon{width:34px;height:34px;background:var(--navy);display:flex;align-items:center;justify-content:center;flex:none}
.info strong{display:block;font-size:14px;color:var(--ink)}
.info span{font-size:11.5px;line-height:18px}
.field{position:absolute;background:#fff;border:1px solid var(--line);font-size:10px;color:var(--muted);padding:9px 12px}
.socials{position:absolute;left:117px;top:4561px;top:378px;display:flex;gap:10px}
.socials span{width:22px;height:22px;border:1px solid var(--navy);display:block}
.submit{position:absolute;left:863px;top:374px;width:155px;height:32px;line-height:32px;background:var(--blue);color:#fff;font-weight:700}

/* footer */
.site-footer{top:4646px;height:78px;border-top:1px solid var(--line)}
.site-footer p{position:absolute;top:32px;width:1200px;text-align:center;font-size:11px;color:var(--ink)}
.site-footer .lang{position:absolute;right:60px;top:56px;font-size:11px;color:var(--ink)}
</style>
</head>
<body>

<header class="section site-header">
  <div class="brand"><span class="brand-mark"></span><span class="brand-name">Treval Buildworks</span></div>
  <div class="search">
    <svg width="13" height="13" viewBox="0 0 13 13"><circle cx="5.5" cy="5.5" r="4.2" fill="none" stroke="#777" stroke-width="1.4"/><line x1="8.6" y1="8.6" x2="12" y2="12" stroke="#777" stroke-width="1.4"/></svg>
    Search
  </div>
  <div class="sign-in">
    <span class="avatar"><svg width="16" height="16" viewBox="0 0 16 16"><circle cx="8" cy="5" r="3.2" fill="#fff"/><path d="M2 15c0-3.5 2.7-5.5 6-5.5s6 2 6 5.5z" fill="#fff"/></svg></span>
    Sign in
  </div>
  <nav class="main-nav"><span>Home</span><span>About us</span><span>Services</span><span>What we do</span><span>Blog</span><span>Testimonial</span><span style="margin-right:0">Contact us</span></nav>
</header>

<section class="section hero">
  <div class="hero-photo" role="img" aria-label="Photo of a finished wood kitchen with pendant lights"></div>
  <div class="hero-shade"></div>
  <svg class="hero-arrow" style="left:36px" width="18" height="34" viewBox="0 0 18 34"><polyline points="16,2 2,17 16,32" fill="none" stroke="#fff" stroke-width="2"/></svg>
  <svg class="hero-arrow" style="right:36px" width="18" height="34" viewBox="0 0 18 34"><polyline points="2,2 16,17 2,32" fill="none" stroke="#fff" stroke-width="2"/></svg>
  <div class="hero-content">
    <h1 class="hero-title">TREVAL BUILDWORKS</h1>
    <p class="hero-sub">Design, build &amp; remodeling contractors</p>
    <div class="hero-actions"><span class="btn solid">Continue with us</span><span class="btn ghost">Get More Info</span></div>
  </div>
</section>

<section class="section intro">
  <h2 class="section-title">Create The Home You've Always Wanted</h2>
  <p class="intro-text">It is a long established fact that a reader will be distracted by the readable content of a page when looking at its layout.<br>It is a long established fact that a reader will be distracted by the readable content of a page</p>
  <div class="feature" style="left:128px">
    <svg width="54" height="64" viewBox="0 0 54 64"><circle cx="27" cy="24" r="19" fill="#f5c623"/><rect x="18" y="42" width="18" height="6" fill="#f5c623"/><rect x="19" y="49" width="16" height="5" fill="#8a8f96"/><rect x="21" y="55" width="12" height="5" fill="#8a8f96"/></svg>
    <h3>Design Ideas</h3>
    <p>There are many variations of passages of Lorem Ipsum available, majority have suffered.</p>
    <a>Read more</a>
  </div>
  <div class="feature" style="left:459px">
    <svg width="64" height="64" viewBox="0 0 64 64"><rect x="22" y="8" width="20" height="10" rx="2" fill="none" stroke="#6a3b1c" stroke-width="4"/><rect x="4" y="16" width="56" height="42" rx="4" fill="#c7521f"/><rect x="4" y="30" width="56" height="4" fill="#8e3512"/><rect x="28" y="28" width="8" height="9" fill="#f2c33a"/></svg>
    <h3>Professionals</h3>
    <p>There are many variations of passages of Lorem Ipsum available, majority have suffered.</p>
    <a>Read more</a>
  </div>
  <div class="feature" style="left:792px">
    <svg width="58" height="64" viewBox="0 0 58 64"><polygon points="29,2 55,17 55,47 29,62 3,47 3,17" fill="#8c98a8"/><polygon points="29,2 55,17 29,32 3,17" fill="#b7c1cd"/><polygon points="29,32 55,17 55,47 29,62" fill="#5c6b7d"/></svg>
    <h3>3D modeling</h3>
    <p>There are many variations of passages of Lorem Ipsum available, majority have suffered.</p>
    <a>Read more</a>
  </div>
</section>

<section class="section jobs">
  <h2 class="section-title">Types of Jobs That We Offers</h2>
  <div class="job-card" style="left:98px">
    <div class="job-photo" role="img" aria-label="Photo of a covered porch with white railings" style="background:linear-gradient(160deg,#7b8794,#4a4f55 60%,#d9d6cf)"><div class="job-label">Custom Carpentry &amp; Finishes</div></div>
    <p>Contrary popular belief, Lorem Ipsum is not simply random text.</p><a>Read More</a>
  </div>
  <div class="job-card" style="left:356px">
    <div class="job-photo" role="img" aria-label="Photo of a wood kitchen with island" style="background:linear-gradient(160deg,#2b1a10,#7a4a26 55%,#3a2414)"><div class="job-label">Custom Carpentry &amp; Finishes</div></div>
    <p>Contrary popular belief, Lorem Ipsum is not simply random text.</p><a>Read More</a>
  </div>
  <div class="job-card" style="left:614px">
    <div class="job-photo" role="img" aria-label="Photo of a dark kitchen with lit cabinets" style="background:linear-gradient(160deg,#16120f,#4d3a2a 50%,#a28a6a)"><div class="job-label">Custom Carpentry &amp; Finishes</div></div>
    <p>Contrary popular belief, Lorem Ipsum is not simply random text.</p><a>Read More</a>
  </div>
  <div class="job-card" style="left:872px">
    <div class="job-photo" role="img" aria-label="Photo of a renovated kitchen with stone counters" style="background:linear-gradient(160deg,#3b2718,#8a5a34 50%,#2a1c12)"><div class="job-label">Custom Carpentry &amp; Finishes</div></div>
    <p>Contrary popular belief, Lorem Ipsum is not simply random text.</p><a>Read More</a>
  </div>
</section>

<section class="section gallery">
  <h2 class="section-title">My Skilled Work Via Before &amp; After Photos</h2>
  <div class="ba-pair" style="left:98px">
    <div class="ba-item"><div class="ba-photo" role="img" aria-label="Before photo of a bare basement room" style="background:linear-gradient(160deg,#5a4220,#b08a3a 55%,#7a5a28)"></div><div class="ba-tag">BEFORE</div></div>
    <div class="ba-item"><div class="ba-photo" role="img" aria-label="After photo of the finished room" style="background:linear-gradient(160deg,#8a3a1e,#3a2a22 55%,#5b4638)"></div><div class="ba-tag">AFTER</div></div>
  </div>
  <div class="ba-pair" style="left:630px">
    <div class="ba-item"><div class="ba-photo" role="img" aria-label="Before photo of an unfinished space" style="background:linear-gradient(160deg,#2a2622,#5a5048 55%,#1e1a17)"></div><div class="ba-tag">BEFORE</div></div>
    <div class="ba-item"><div class="ba-photo" role="img" aria-label="After photo of a finished kitchen" style="background:linear-gradient(160deg,#1a1410,#6e5238 50%,#b8935e)"></div><div class="ba-tag">AFTER</div></div>
  </div>
</section>

<section class="section why">
  <div class="why-art" role="img" aria-label="Pencil sketch of a modern two-storey house"></div>
  <div class="why-panel">
    <div class="why-body">
      <h2>Why Choose Us?</h2>
      <h4>Modeling of New Spaces and it would be nice to show</h4>
      <p>There are many variations of passages of Lorem Ipsum available, but the majority have suffered alteration in some form, by injected humour, or randomised words which don't look even slightly believable. If you are going to use a passage of Lorem Ipsum, you need to be sure there isn't anything embarrassing hidden in the middle of text.</p>
      <p>All the Lorem Ipsum generators on the Internet tend to repeat predefined chunks as necessary, making this the first true generator on the Internet. It uses a dictionary</p>
      <span class="btn">Read More</span>
    </div>
  </div>
</section>

<section class="section browse">
  <div class="browse-box">
    <h3>Browse Professionals</h3>
    <p>There are many variations of passages of Lorem Ipsum available, but the majority have suffered alteration in some form, by injected humour, or randomised words which don't look even slightly believable. If you are going to use a passage of Lorem Ipsum, you need to be sure there isn't anything embarrassing hidden in the middle of text. There are many variations of passages of Lorem Ipsum available</p>
    <p>There are many variations of passages of Lorem Ipsum available, but the majority have suffered alteration in some form, by injected humour, or randomised words which don't look even slightly believable.</p>
  </div>
  <div class="cta-box" role="img" aria-label="Dark blue panel over a tools photo">
    <h3>Make your work<br>quick &amp; easy</h3>
    <span class="btn">Mail Us</span>
  </div>
  <div class="pro-card" style="left:98px">
    <div class="pro-photo" role="img" aria-label="Photo of a traditional kitchen" style="background:linear-gradient(160deg,#1c1410,#5a3a24 50%,#2a1c14)"></div>
    <h4>Traditional Kitchen</h4>
    <p>It is a long established fact that a reader will be distracted by the readable content of a page</p>
    <div class="pro-meta"><span>14 hours ago</span><span>160K Saves | 20 Questions</span></div>
  </div>
  <div class="pro-card" style="left:441px">
    <div class="pro-photo" role="img" aria-label="Photo of a traditional kitchen with island" style="background:linear-gradient(160deg,#5a3a22,#b07a48 50%,#3a2616)"></div>
    <h4>Traditional Kitchen</h4>
    <p>It is a long established fact that a reader will be distracted by the readable content of a page</p>
    <div class="pro-meta"><span>14 hours ago</span><span>160K Saves | 20 Questions</span></div>
  </div>
  <div class="pro-card" style="left:788px">
    <div class="pro-photo" role="img" aria-label="Photo of a traditional kitchen with hardwood floor" style="background:linear-gradient(160deg,#2a1a10,#6e4426 50%,#1c120c)"></div>
    <h4>Traditional Kitchen</h4>
    <p>It is a long established fact that a reader will be distracted by the readable content of a page</p>
    <div class="pro-meta"><span>14 hours ago</span><span>160K Saves | 20 Questions</span></div>
  </div>
</section>

<section class="section video">
  <div class="video-bg" role="img" aria-label="Dark photo of a kitchen interior behind a video"></div>
  <h2>3D CAD and Modeling of New Spaces</h2>
  <svg class="play" width="60" height="60" viewBox="0 0 60 60"><circle cx="30" cy="30" r="27" fill="none" stroke="#fff" stroke-width="2.5"/><polygon points="24,18 42,30 24,42" fill="none" stroke="#fff" stroke-width="2.5" stroke-linejoin="round"/></svg>
</section>

<section class="section design">
  <h2 class="section-title">Design To 3D Modeling</h2>
  <div class="cta-box" role="img" aria-label="Dark blue panel over a renovation photo">
    <h3>Whole House<br>Renovation</h3>
    <span class="btn">Mail Us</span>
  </div>
  <div class="work-box">
    <h3>Show some of that work</h3>
    <p>There are many variations of passages of Lorem Ipsum available, but the majority have suffered alteration in some form, by injected humour, or randomised words which don't look even slightly believable. If you are going to use a passage of Lorem Ipsum, you need to be sure there isn't anything embarrassing hidden in the middle of text. There are many variations of passages of Lorem Ipsum available</p>
    <p>There are many variations of passages of Lorem Ipsum available, but the majority have suffered alteration in some form, by injected humour, or randomised words which don't look even slightly believable.</p>
  </div>
</section>

<section class="section contact">
  <h2 class="section-title">Contact Us</h2>
  <div class="info" style="left:142px">
    <span class="info-icon"><svg width="16" height="16" viewBox="0 0 16 16"><path d="M3 1l3 3-2 2c1 2 3 4 5 5l2-2 3 3-2 3C6 14 2 10 1 3z" fill="#fff"/></svg></span>
    <div><strong>Call us</strong><span>+1 555 0142 218</span></div>
  </div>
  <div class="info" style="left:425px">
    <span class="info-icon"><svg width="16" height="12" viewBox="0 0 16 12"><rect x="1" y="1" width="14" height="10" fill="none" stroke="#fff" stroke-width="1.5"/><polyline points="1,1 8,7 15,1" fill="none" stroke="#fff" stroke-width="1.5"/></svg></span>
    <div><strong>Email</strong><span>hello@trevalbuild.com</span></div>
  </div>
  <div class="info" style="left:740px">
    <span class="info-icon"><svg width="12" height="16" viewBox="0 0 12 16"><path d="M6 15C2 10 1 8 1 6a5 5 0 0 1 10 0c0 2-1 4-5 9z" fill="#fff"/><circle cx="6" cy="6" r="2" fill="#18314f"/></svg></span>
    <div><strong>Address</strong><span>Harlow Court 12, Birchwood Lane<br>ELM 4410 Elmstead</span></div>
  </div>
  <div class="field" style="left:117px;top:255px;width:441px;height:34px">Name</div>
  <div class="field" style="left:117px;top:312px;width:441px;height:34px">Mail Id</div>
  <div class="field" style="left:580px;top:255px;width:438px;height:94px">Message</div>
  <div class="socials"><span></span><span></span><span></span><span></span><span></span></div>
  <span class="btn submit">Submit Message</span>
</section>

<footer class="section site-footer">
  <p>Copyright@2017Company Name , all rights Reserved</p>
  <span class="lang">C15</span>
</footer>

</body>
</html>
```